Veltrane Group Business Card Design

The CEO is looking for a new trendy look for his business card.
You can stay with current branding or come up with something new/creative. It can be 3D, including Medical Office buildings. You can use our logo in a variety of colors. Please include name, title, company name, company website, email address, cell number

Target Market(s)

Real Estate Development and Construction

Industry/Entity Type

Health care real estate

Contact Information for Business Card

Rohesh Kamdar, CEO M-604.781.2249 E-roheshkamdar@veltrane.com Address:4180 Lindqvist Ave, Tampa, FL 33482 www.veltrane.com

Font styles to use
Other font styles liked:
• Be creative

Requirements
Must have
• Creative, trendy look
Nice to have
• Please go to our website to get a feel- www. veltrane.com
Should not have
• small fonts

```html
<!DOCTYPE html>
<html lang="en">
<head>
<meta charset="utf-8">
<title>Veltrane Group Business Card</title>
<link rel="stylesheet" href="https://fonts.googleapis.com/css2?family=Arimo:wght@400;700&display=swap">
<style>
  :root {
    --brand-red: #b01f2a;
    --brand-navy: #1c2f55;
    --paper: #ffffff;
    --ink: #3a3a3a;
    --rule: #c9c9c9;
    --backdrop: #2a2a2c;
  }
  * { box-sizing: border-box; margin: 0; padding: 0; }
  html, body {
    width: 1200px; height: 874px; overflow: hidden;
    background: var(--backdrop);
    font-family: "Arimo", Arial, sans-serif;
  }
  .stage { position: relative; width: 1200px; height: 874px; }
  .card {
    position: absolute; left: 320px;
    width: 560px; height: 320px;
    border-radius: 22px; overflow: hidden;
  }
  .card-front { top: 100px; background: var(--brand-red); color: var(--paper); }
  .card-back { top: 454px; background: var(--paper); }

  .front-name {
    position: absolute; left: 0; right: 0; top: 108px;
    text-align: center; font-weight: 700; font-size: 64px; letter-spacing: -1px;
  }
  .front-url {
    position: absolute; left: 0; right: 0; bottom: 30px;
    text-align: center; font-size: 14px;
  }

  .back-wave { position: absolute; left: 0; bottom: 0; width: 560px; height: 140px; }
  .back-name {
    position: absolute; left: 34px; top: 92px; width: 210px;
    color: var(--brand-red); font-weight: 700; font-size: 38px; line-height: 1; letter-spacing: -1px;
  }
  .back-divider {
    position: absolute; left: 262px; top: 56px; width: 1px; height: 150px;
    background: var(--rule);
  }
  .contact { position: absolute; left: 284px; top: 60px; color: var(--ink); }
  .contact-name { color: var(--brand-red); font-weight: 700; font-size: 22px; }
  .contact-title { color: var(--brand-navy); font-size: 13px; margin-bottom: 12px; }
  .contact-address { font-size: 14px; line-height: 1.3; margin-bottom: 10px; }
  .contact-line { display: flex; align-items: center; gap: 8px; font-size: 14px; line-height: 1.4; }
  .contact-line svg { width: 12px; height: 12px; flex: none; }
</style>
</head>
<body>
<main class="stage">
  <section class="card card-front">
    <div class="front-name">Veltrane Group</div>
    <div class="front-url">www.veltrane.com</div>
  </section>

  <section class="card card-back">
    <svg class="back-wave" viewBox="0 0 560 140" preserveAspectRatio="none" aria-hidden="true">
      <path d="M0 20 Q260 130 560 122 L560 140 L0 140 Z" fill="var(--brand-red)"/>
      <path d="M0 14 Q260 124 560 116" fill="none" stroke="var(--brand-navy)" stroke-width="4"/>
    </svg>
    <div class="back-name">Veltrane Group</div>
    <div class="back-divider"></div>
    <div class="contact">
      <div class="contact-name">Rohesh Kamdar</div>
      <div class="contact-title">CEO</div>
      <div class="contact-address">4180 Lindqvist Ave, Tampa<br>FL 33482</div>
      <div class="contact-line">
        <svg viewBox="0 0 12 12"><path d="M2 1h3l1 3-1.5 1a6 6 0 0 0 2.5 2.5L8 6l3 1v3a1 1 0 0 1-1 1A9 9 0 0 1 1 2a1 1 0 0 1 1-1z" fill="var(--brand-red)"/></svg>
        604.781.2249
      </div>
      <div class="contact-line">
        <svg viewBox="0 0 12 12"><rect x="0.5" y="2.5" width="11" height="7" fill="var(--brand-red)"/><path d="M0.5 2.5 6 7l5.5-4.5" fill="none" stroke="#fff" stroke-width="1"/></svg>
        roheshkamdar@veltrane.com
      </div>
      <div class="contact-line">
        <svg viewBox="0 0 12 12"><circle cx="6" cy="6" r="5.5" fill="var(--brand-red)"/></svg>
        www.veltrane.com
      </div>
    </div>
  </section>
</main>
</body>
</html>
```